Create Social Media design templates for Online-Education-Startup

We are an online platform for pupils who provide group courses and on demand individual tutroing lessons. Our core values are personalisation, family and success. We need a holistic social media design concept which includes nine possible layouts for Instagram posts which reflect our values and promote not only our offerings and special deals but also support in building our brand image (for example: telling company history, daily news, funny facts, getting to know the team etc.).
Additionally, we need design elements for our YouTube channel:
-Videocover
-Cover Image for the channel

Our main colour is orange (RGB-Code: 255;105;31) and additional colours white, black, and grey. For the reference have a look at our website: www.lernvolta.de.

Target Market(s)

We want to attract customers to our online tutoring courses and build a brand.

Industry/Entity Type

Education / Tutoring

Font styles to use
Sans Serif

Requirements
Must have
• Familiarize yourself with the style of our website. The designs should fit as well as possible.

```html
<!DOCTYPE html>
<html lang="de">
<head>
<meta charset="utf-8">
<title>Lernvolta – Social Media Vorlagen</title>
<link href="https://fonts.googleapis.com/css2?family=Roboto:ital,wght@0,400;0,700;1,700;1,900&family=Anton&family=Poppins:wght@400;600;800&family=Allura&display=swap" rel="stylesheet">
<style>
  :root{
    --orange:#ff691f;
    --orange-deep:#e8501a;
    --orange-soft:#ff8a45;
    --red:#c8102e;
    --ink:#111111;
    --grey:#f1f1f1;
    --white:#ffffff;
  }
  *{box-sizing:border-box;margin:0;padding:0}
  html,body{width:1200px;height:848px;overflow:hidden;background:var(--white)}
  body{position:relative;font-family:"Roboto",sans-serif;color:var(--ink)}
  .post{position:absolute;width:231px;height:231px;overflow:hidden;background:var(--white);box-shadow:0 1px 4px rgba(0,0,0,.35)}
  .post > svg.bg{position:absolute;inset:0;width:231px;height:231px}
  .abs{position:absolute}
  .brand{position:absolute;display:flex;align-items:center;gap:3px}
  .brand-dot{width:14px;height:14px;border:1.6px solid var(--orange);border-radius:50%}
  .brand-name{font-family:"Roboto",sans-serif;font-weight:700;font-size:5px;line-height:1.1;color:var(--ink)}
  .brand-sub{font-weight:400;display:block}
  .photo{position:absolute;border-radius:50%}
  .h-italic{font-family:"Roboto",sans-serif;font-style:italic;font-weight:700;color:var(--ink)}
  .body{font-size:4.3px;line-height:1.4;color:var(--ink)}
  .cta{position:absolute;text-align:right;line-height:1.15}
  .cta small{display:block;font-size:4.5px}
  .cta b{font-size:8px;font-weight:700}
  .globe{width:16px;height:16px;color:var(--white)}
  .quote-bar{border-left:1.5px solid var(--orange);padding-left:4px}
  .pill{position:absolute;background:var(--orange);color:var(--white);font-weight:700;border-radius:0 12px 12px 0;display:flex;align-items:center}
  .url-line{position:absolute;display:flex;align-items:center;gap:4px;font-size:7px}
  .globe-red{width:11px;height:11px;color:var(--red)}

  #p1{left:74px;top:32px;background:var(--grey)}
  #p2{left:350px;top:32px}
  #p3{left:626px;top:32px;background:#f5f5f5}
  #p4{left:903px;top:32px}
  #p5{left:74px;top:310px}
  #p6{left:350px;top:310px;background:#f6f6f6}
  #p7{left:626px;top:310px}
  #p8{left:903px;top:310px}
  #p9{left:474px;top:590px;background:#f4f4f4}

  .condensed{font-family:"Anton",sans-serif;color:var(--ink);text-transform:uppercase}
  .script{font-family:"Allura",cursive;color:var(--ink)}
  .pop{font-family:"Poppins",sans-serif}
  .option{display:flex;align-items:center;gap:3px;font-family:"Poppins",sans-serif;font-size:5px}
  .tick{width:10px;height:10px}
</style>
</head>
<body>
<svg width="0" height="0" style="position:absolute">
  <defs>
    <symbol id="globe" viewBox="0 0 20 20">
      <circle cx="10" cy="10" r="9" fill="none" stroke="currentColor" stroke-width="1.6"/>
      <ellipse cx="10" cy="10" rx="4" ry="9" fill="none" stroke="currentColor" stroke-width="1.3"/>
      <path d="M1 10h18M2.5 5.5h15M2.5 14.5h15M10 1v18" stroke="currentColor" stroke-width="1.2" fill="none"/>
    </symbol>
    <symbol id="tick" viewBox="0 0 20 20">
      <circle cx="10" cy="10" r="9" fill="none" stroke="#ff691f" stroke-width="2"/>
      <circle cx="10" cy="10" r="6.5" fill="#ff691f"/>
      <path d="M7 10.2l2 2 4-4.4" stroke="#fff" stroke-width="1.8" fill="none" stroke-linecap="round"/>
    </symbol>
  </defs>
</svg>

<!-- 1: Unsere Reise -->
<section class="post" id="p1">
  <div class="abs" role="img" aria-label="Foto einer lächelnden Schülerin mit Brille und Büchern" style="left:120px;top:0;width:111px;height:210px;background:linear-gradient(160deg,#cfd6df,#7d94b3 60%,#c9a08a)"></div>
  <svg class="bg" viewBox="0 0 231 231">
    <path d="M0 180 C60 200 120 160 231 180 L231 231 L0 231Z" fill="var(--orange-soft)"/>
    <path d="M0 192 C70 215 140 170 231 195 L231 231 L0 231Z" fill="var(--orange)"/>
    <path d="M0 196 C60 222 140 180 231 204" stroke="#fff" stroke-width="1.4" fill="none"/>
  </svg>
  <div class="brand" style="left:24px;top:24px"><span class="brand-dot"></span><span class="brand-name">Lernvolta<span class="brand-sub">Bildungsinstitut</span></span></div>
  <h2 class="abs h-italic" style="left:23px;top:52px;font-size:14.5px;line-height:1.45">Unsere Reise:<br>Von der<br>Leidenschaft<br>zur Wirkung</h2>
  <p class="abs body" style="left:23px;top:142px;width:88px">Bei Lernvolta haben wir mit dem Traum begonnen, Bildung für jeden Schüler zu personalisieren. Heute sind wir stolz darauf, unzählige Familien auf dem Weg zum schulischen Erfolg zu unterstützen!</p>
  <div class="cta" style="right:32px;top:200px"><small>Melde dich jetzt auf</small><b>www.lernvolta.de</b></div>
  <svg class="globe abs" style="right:12px;top:200px"><use href="#globe"/></svg>
</section>

<!-- 2: Wusstest du schon -->
<section class="post" id="p2">
  <svg class="bg" viewBox="0 0 231 231">
    <path d="M140 0 L231 0 L231 110 C215 60 180 30 140 0Z" fill="var(--orange)"/>
    <path d="M0 190 L110 200 C150 190 200 120 231 100 L231 231 L0 231Z" fill="var(--orange)"/>
    <path d="M40 231 C120 210 190 170 231 140 L231 231Z" fill="var(--orange-soft)"/>
    <circle cx="190" cy="112" r="68" fill="var(--orange)"/>
    <circle cx="193" cy="112" r="60" fill="#fff"/>
  </svg>
  <div class="photo" role="img" aria-label="Foto einer Mutter und Tochter am Laptop" style="left:135px;top:55px;width:116px;height:116px;background:linear-gradient(150deg,#b9b3ad,#8a7467 60%,#d9c5bb)"></div>
  <div class="brand" style="left:24px;top:17px"><span class="brand-dot"></span><span class="brand-name">Lernvolta<span class="brand-sub">Bildungsinstitut</span></span></div>
  <h2 class="abs h-italic" style="left:12px;top:50px;font-size:22px;line-height:1.45">Wusstest du<br>schon?</h2>
  <p class="abs body quote-bar" style="left:16px;top:114px;width:76px">Eine Gruppe von Flamingos wird 'Flamboyance' genannt – genau wie unsere Schüler, die sich durch ihren schulischen Erfolg abheben</p>
  <div class="abs" style="left:101px;top:126px;width:60px;height:60px;border-radius:50%;background:var(--orange-deep);color:var(--ink);font-size:5px;text-align:center;display:flex;align-items:center;justify-content:center;line-height:1.25;padding:4px">SCHLIESSE DICH UNSEREN KURSEN AN UND HEBE DICH AB WIE EIN FLAMINGO!</div>
  <div class="cta" style="right:42px;top:200px"><small>Melde dich jetzt auf</small><b>www.lernvolta.de</b></div>
  <svg class="globe abs" style="right:22px;top:199px"><use href="#globe"/></svg>
</section>

<!-- 3: Neuigkeiten -->
<section class="post" id="p3">
  <svg class="bg" viewBox="0 0 231 231">
    <path d="M95 231 C85 150 110 60 200 58 L231 58 L231 231Z" fill="var(--orange)"/>
  </svg>
  <div class="abs" role="img" aria-label="Foto von Händen mit Stift und Laptop auf einem Schreibtisch" style="left:103px;top:66px;width:128px;height:125px;border-radius:70px 0 0 70px;background:linear-gradient(135deg,#f3e4cf,#d6b89a 50%,#3c3c3c)"></div>
  <div class="brand" style="left:24px;top:13px"><span class="brand-dot"></span><span class="brand-name">Lernvolta<span class="brand-sub">Bildungsinstitut</span></span></div>
  <h2 class="abs h-italic" style="left:21px;top:40px;font-size:14px;line-height:1.5">Neuigkeiten: Neue Kurse<br>starten bald!</h2>
  <div class="abs" style="left:19px;top:102px;width:100px;height:59px;background:rgba(255,255,255,.93);border-radius:4px;padding:7px 7px"><p style="font-size:5px;line-height:1.5">Wir freuen uns, neue Kurse für Mathematik, Naturwissenschaften und mehr anzukündigen. Bleibe dran für die Einschreibetermine</p></div>
  <div class="pill" style="left:0;top:174px;width:98px;height:19px;padding-left:6px;font-size:8.5px">Melde dich jetzt auf</div>
  <div class="url-line" style="left:19px;top:199px"><svg class="globe-red"><use href="#globe"/></svg>www.lernvolta.de</div>
</section>

<!-- 4: Entfessle dein volles Potenzial -->
<section class="post" id="p4">
  <svg class="bg" viewBox="0 0 231 231">
    <path d="M0 0 L85 0 C70 20 55 30 40 35 L0 40Z" fill="var(--orange)"/>
    <path d="M0 231 L0 180 C70 170 130 210 231 160 L231 231Z" fill="var(--orange)"/>
    <path d="M0 231 C80 220 150 215 231 185 L231 231Z" fill="var(--orange-deep)"/>
    <circle cx="58" cy="107" r="76" fill="var(--orange)"/>
    <rect x="18" y="192" width="84" height="18" rx="9" fill="var(--orange-soft)" opacity=".7"/>
  </svg>
  <div class="photo" role="img" aria-label="Foto von Studierenden in einem Hörsaal" style="left:-10px;top:40px;width:130px;height:130px;background:linear-gradient(160deg,#b88a5c,#8b6a4e 55%,#dcd0c4)"></div>
  <div class="brand" style="left:153px;top:26px"><span class="brand-dot"></span><span class="brand-name">Lernvolta<span class="brand-sub">Bildungsinstitut</span></span></div>
  <h2 class="abs h-italic" style="right:12px;top:52px;font-size:13.3px;line-height:1.42;text-align:right">Entfessle dein<br>volles Potenzial<br>mit unseren<br>Expertenkursen!</h2>
  <p class="abs body" style="right:12px;top:137px;width:98px;text-align:right;font-size:4px">Schließe dich unseren Gruppenkursen an oder buche individuelle Nachhilfe. Starte noch heute deine Lernreise mit maßgeschneiderten Lektionen nur für dich!</p>
  <div class="cta" style="right:39px;top:195px"><small>Melde dich jetzt auf</small><b>www.lernvolta.de</b></div>
  <svg class="globe abs" style="right:20px;top:194px"><use href="#globe"/></svg>
</section>

<!-- 5: Sonderangebot -->
<section class="post" id="p5">
  <svg class="bg" viewBox="0 0 231 231">
    <path d="M110 0 L231 0 L231 110 C200 50 160 30 110 0Z" fill="var(--orange)"/>
    <path d="M0 190 L110 200 C150 190 200 130 231 110 L231 231 L0 231Z" fill="var(--orange)"/>
    <path d="M40 231 C120 210 190 170 231 150 L231 231Z" fill="var(--orange-soft)"/>
    <circle cx="185" cy="112" r="68" fill="var(--orange)"/>
    <circle cx="189" cy="112" r="60" fill="#fff"/>
  </svg>
  <div class="photo" role="img" aria-label="Foto einer Mutter und Tochter am Laptop" style="left:131px;top:55px;width:116px;height:116px;background:linear-gradient(150deg,#b9b3ad,#8a7467 60%,#d9c5bb)"></div>
  <div class="brand" style="left:24px;top:17px"><span class="brand-dot"></span><span class="brand-name">Lernvolta<span class="brand-sub">Bildungsinstitut</span></span></div>
  <h2 class="abs h-italic" style="left:17px;top:43px;font-size:12.8px;line-height:1.5">Sonderangebot:<br>20% Rabatt auf<br>alle Kurse diesen<br>Monat!</h2>
  <p class="abs body quote-bar" style="left:17px;top:131px;width:82px">Schließe dich unseren Gruppenkursen an oder buche individuelle Nachhilfe. Starte noch heute deine Lernreise mit maßgeschneiderten Lektionen nur für dich!</p>
  <div class="cta" style="right:42px;top:200px"><small>Melde dich jetzt auf</small><b>www.lernvolta.de</b></div>
  <svg class="globe abs" style="right:22px;top:199px"><use href="#globe"/></svg>
</section>

<!-- 6: Lerne unser Expertenteam kennen -->
<section class="post" id="p6">
  <svg class="bg" viewBox="0 0 231 231">
    <path d="M231 0 L170 0 C140 10 110 50 108 100 C106 170 160 215 231 218Z" fill="var(--orange)"/>
    <path d="M231 2 L178 2 C150 15 123 55 122 100 C121 160 165 200 231 205Z" fill="#1a2a44"/>
  </svg>
  <div class="abs" role="img" aria-label="Foto eines Teams am Besprechungstisch mit Laptops, von oben" style="left:125px;top:4px;width:106px;height:199px;border-radius:100px 0 0 100px;background:linear-gradient(140deg,#6b4a33,#8e6b52 45%,#d8d8d8)"></div>
  <div class="brand" style="left:19px;top:21px"><span class="brand-dot"></span><span class="brand-name">Lernvolta<span class="brand-sub">Bildungsinstitut</span></span></div>
  <h2 class="abs condensed" style="left:19px;top:48px;font-size:17.5px;line-height:1.18;font-weight:400">Lerne<br>unser<br>Expertente<br>am kennen</h2>
  <p class="abs condensed" style="left:17px;top:133px;width:76px;font-size:5.2px;line-height:1.45;text-align:center;text-transform:none">Wir haben ein leidenschaftliches und engagiertes Tutorenteam, das sicherstellt, dass jeder Schüler sein volles Potenzial ausschöpft!</p>
  <p class="abs condensed" style="left:19px;top:187px;font-size:5.8px">Lerne uns besser kennen auf</p>
  <div class="pill" style="left:19px;top:198px;width:79px;height:11px;border-radius:2px;font-size:5px;padding-left:4px;gap:2px"><svg style="width:6px;height:6px;color:#fff"><use href="#globe"/></svg>www.lernvolta.de</div>
  <p class="abs condensed" style="left:22px;top:213px;font-size:4.3px;text-transform:none">und treffe die Gesichter hinter deinem Erfolg.</p>
</section>

<!-- 7: Erfolgsgeschichten -->
<section class="post" id="p7">
  <svg class="bg" viewBox="0 0 231 231">
    <path d="M185 90 A48 48 0 1 1 231 150" stroke="var(--ink)" stroke-width="6" fill="none"/>
    <circle cx="176" cy="77" r="45" fill="var(--orange)"/>
    <circle cx="168" cy="157" r="3.5" stroke="var(--ink)" stroke-width="1.3" fill="none"/>
    <path d="M153 18v20M191 18v20" stroke="#666" stroke-width=".5" stroke-dasharray="2 1"/>
    <path d="M218 51h6M221 48v6" stroke="var(--orange)" stroke-width="1"/>
  </svg>
  <div class="photo" role="img" aria-label="Foto von Händen an Tablet und Notizen auf einem Tisch" style="left:138px;top:40px;width:76px;height:76px;background:linear-gradient(140deg,#e9eef4,#9fb3c8 55%,#4c5560)"></div>
  <div class="brand" style="left:19px;top:46px"><span class="brand-dot" style="width:19px;height:19px"></span><span class="brand-name" style="font-size:7px">Lernvolta<span class="brand-sub">Bildungsinstitut</span></span></div>
  <h2 class="abs script" style="left:12px;top:86px;font-size:17px;line-height:1.0;font-weight:400;width:140px">Erfolgsgeschichten:<br>Sieh, was unsere<br>Schüler erreichen!</h2>
  <p class="abs" style="left:16px;top:153px;width:136px;font-family:'Poppins',sans-serif;font-size:4.2px;line-height:1.35">Von Schwierigkeiten in Mathe bis hin zu herausragenden Leistungen: [Schülername] ist eine von vielen Erfolgsgeschichten. Wir sind stolz darauf, Schüler auf dem Weg zu ihren Zielen zu unterstützen.</p>
  <div class="cta" style="right:30px;top:186px;font-family:'Poppins',sans-serif"><b style="color:var(--orange);font-size:7px;font-weight:600;display:block">Melde dich jetzt auf</b><small style="font-size:5.5px">www.lernvolta.de</small></div>
</section>

<!-- 8: Erfolg beginnt -->
<section class="post" id="p8">
  <div class="abs" role="img" aria-label="Foto einer lernenden Frau mit Kopfhörern vor einem Bücherregal" style="left:0;top:4px;width:231px;height:130px;background:linear-gradient(120deg,#eeeae3,#cfc3b3 40%,#7b5d63 70%,#efe8e0)"></div>
  <svg class="bg" viewBox="0 0 231 231">
    <path d="M0 60 C30 100 60 115 110 110 C160 105 190 90 231 100 L231 231 L0 231Z" fill="var(--orange)"/>
    <path d="M0 120 C60 115 100 130 150 120 C190 112 210 100 231 105 L231 231 L0 231Z" fill="var(--orange-deep)"/>
    <circle cx="40" cy="128" r="5" fill="#ff4f4f" opacity=".8"/>
    <circle cx="33" cy="122" r="2" fill="#fff"/>
  </svg>
  <div class="brand" style="left:10px;top:16px"><span class="brand-dot"></span><span class="brand-name">Lernvolta<span class="brand-sub">Bildungsinstitut</span></span></div>
  <h2 class="abs pop" style="left:31px;top:134px;font-size:8.6px;line-height:1.45;color:var(--white);font-weight:800">ERFOLG BEGINNT MIT<br>DEM ERSTEN SCHRITT</h2>
  <p class="abs pop" style="left:31px;top:163px;width:108px;font-size:4.4px;line-height:1.45;color:var(--white)">Jede Reise beginnt mit der Entscheidung, es zu versuchen. Mach noch heute den ersten Schritt und lass uns dich auf deinem Weg zum schulischen Erfolg begleiten.</p>
  <p class="abs pop" style="left:37px;top:197px;font-size:4.5px;font-weight:800;color:var(--white)">BEREIT ZUM START?</p>
  <div class="cta pop" style="right:40px;top:197px;color:var(--white)"><small>Melde dich jetzt auf</small><small>www.lernvolta.de</small></div>
  <svg class="abs" style="right:32px;top:200px;width:8px;height:8px;color:#fff"><use href="#globe"/></svg>
</section>

<!-- 9: Welches Fach -->
<section class="post" id="p9">
  <svg class="bg" viewBox="0 0 231 231">
    <path d="M231 60 L140 60 C100 70 80 120 110 170 C130 200 180 192 231 192Z" fill="var(--orange)"/>
    <path d="M100 160 C120 195 170 196 231 192 L231 200 C170 205 115 200 100 160Z" fill="var(--red)"/>
  </svg>
  <div class="abs" role="img" aria-label="Foto eines Schreibtischs mit Monitor, Lampe und Stiften" style="left:104px;top:66px;width:127px;height:123px;border-radius:70px 0 0 70px;background:linear-gradient(140deg,#f1f3f5,#c9d3db 50%,#7a8088)"></div>
  <div class="brand" style="left:162px;top:16px"><span class="brand-dot"></span><span class="brand-name">Lernvolta<span class="brand-sub">Bildungsinstitut</span></span></div>
  <h2 class="abs pop" style="left:19px;top:32px;font-size:13.5px;line-height:1.12;font-weight:800">Welches Fach<br>möchtest du<br>verbessern?</h2>
  <p class="abs pop" style="left:22px;top:93px;font-size:9.5px;font-weight:600">Optionen:</p>
  <div class="abs" style="left:19px;top:107px;width:120px;height:44px;background:rgba(255,255,255,.95);border-radius:5px;padding:6px 5px;display:grid;grid-template-columns:46px 70px;row-gap:9px">
    <span class="option"><svg class="tick"><use href="#tick"/></svg>Mathematik</span>
    <span class="option"><svg class="tick"><use href="#tick"/></svg>Naturwissenschaften</span>
    <span class="option"><svg class="tick"><use href="#tick"/></svg>Sprachen</span>
    <span class="option" style="line-height:1.2"><svg class="tick"><use href="#tick"/></svg>Sonstiges<br>(Kommentiere unten)</span>
  </div>
  <div class="pill pop" style="left:0;top:175px;width:98px;height:19px;padding-left:17px;font-size:7px;background:linear-gradient(90deg,var(--red),var(--orange))">Melde dich jetzt auf</div>
  <div class="url-line pop" style="left:19px;top:202px;font-size:6px"><svg class="globe-red"><use href="#globe"/></svg>www.lernvolta.de</div>
</section>
</body>
</html>
```